Garland Custom Boats Website update

I would like an updated website to my current site (Garlandboats.com).
I have an updated logo i would like to incorporate.
24 pages , would like to integrate videos of the boats (that i can upload later)

Target Market(s)

Professional and Commercial boat owners

Industry/Entity Type

Custom Boat Manufacturing

Coding

Coded - Design and coding required

Number of Pages Required

5+ page

Font styles to use
Serif

Requirements
Must have
• Easy to read, well laid-out, and video integration
Nice to have
• Fresh up to date look

```html
<!DOCTYPE html>
<html lang="en">
<head>
<meta charset="utf-8">
<title>Garland Custom Boats</title>
<link href="https://fonts.googleapis.com/css2?family=Exo+2:ital,wght@1,800;1,900&family=Roboto:wght@400;500;700&display=swap" rel="stylesheet">
<style>
:root{
  --red:#c0141c;
  --blue:#0b2f93;
  --blue-dark:#06206e;
  --ink:#111;
  --text:#444;
  --muted:#e4e6ec;
  --pale:#dbe7fb;
  --white:#fff;
}
*{box-sizing:border-box;margin:0;padding:0}
html,body{width:1200px;height:5199px;overflow:hidden}
body{font-family:"Roboto",sans-serif;color:var(--ink);background:var(--white);position:relative}
.abs{position:absolute}
.display{font-family:"Exo 2",sans-serif;font-style:italic;font-weight:900}
.btn{position:absolute;background:var(--red);color:var(--white);font:700 15px "Roboto",sans-serif;display:flex;align-items:center;justify-content:center;border-radius:0 14px 0 0;text-transform:uppercase}
.ph{position:absolute}

.topbar{position:absolute;top:0;left:0;width:1200px;height:40px;background:var(--red);color:var(--white);font-size:13px;font-weight:500}
.topbar .item{position:absolute;top:0;height:40px;display:flex;align-items:center;gap:12px;white-space:nowrap}
.topbar .sep{position:absolute;top:8px;width:2px;height:24px;background:var(--white)}
.icon-box{width:22px;height:22px;display:flex;align-items:center;justify-content:center}

.brand{position:absolute;left:112px;top:58px;width:290px;height:80px}
.brand .name{font:700 34px "Roboto",sans-serif;color:var(--blue);letter-spacing:1px;line-height:40px}
.brand .sub{font:700 14px "Roboto",sans-serif;color:var(--blue);letter-spacing:3px}
.reviews{position:absolute;left:500px;top:62px;font-size:14px}
.reviews .stars{color:#f4b400;font-size:13px}
.search{position:absolute;left:762px;top:78px;width:326px;height:42px;background:var(--muted);border-radius:6px;font-size:12px;color:#666;display:flex;align-items:center;padding:0 22px;justify-content:space-between}

.nav{position:absolute;top:148px;left:0;width:1200px;height:52px;background:var(--blue)}
.nav ul{list-style:none;display:flex;position:absolute;left:112px;top:13px}
.nav li{color:var(--white);font-size:13px;font-weight:500;padding:6px 16px;margin-right:8px}
.nav li.active{background:var(--red);border-radius:3px}
.nav .cta{position:absolute;right:112px;top:0;height:52px;width:162px;background:var(--red);color:var(--white);font-weight:700;font-size:14px;display:flex;align-items:center;justify-content:center;border-radius:0 30px 0 0}

.hero{position:absolute;top:200px;left:0;width:1200px;height:600px}
.hero h1{position:absolute;left:112px;top:52px;color:var(--white);font-size:58px;line-height:66px;letter-spacing:1px}
.dots{position:absolute;left:572px;top:496px;display:flex;gap:8px}
.dots span{width:12px;height:12px;border-radius:50%;background:var(--white)}
.dots span.on{background:var(--red)}

.sec-title{position:absolute;left:0;width:1200px;text-align:center}
.sec-title .ghost{position:absolute;left:0;right:0;font-size:76px;color:#e9ebf2;top:-18px;white-space:nowrap}
.sec-title .solid{position:relative;font-size:42px;color:var(--ink)}
.sec-title .solid em{color:var(--blue);font-style:italic}

.card{position:absolute;background:var(--white);box-shadow:0 2px 10px rgba(0,0,0,.18);border-radius:4px}
.card .pic{position:absolute;left:10px;top:14px;right:10px;border-radius:4px}
.card .label{position:absolute;left:0;right:0;text-align:center;font-size:21px;color:#222}
.card.featured{border:3px solid var(--blue)}
.card.featured .label{color:var(--blue)}

.about-panel{position:absolute;left:600px;top:1428px;width:600px;height:522px;background:var(--pale)}
.about-panel p{position:absolute;left:44px;width:450px;font-size:13.5px;line-height:31px;color:var(--text)}

.partners{position:absolute;top:2000px;left:0;width:1200px;height:110px}
.partners h3{position:absolute;left:112px;top:28px;font-size:29px;line-height:38px;color:var(--ink)}
.partners h3 em{color:var(--blue)}
.partner{position:absolute;top:40px;height:44px;display:flex;align-items:center;gap:10px;font:700 21px "Roboto",sans-serif;color:var(--ink);white-space:nowrap}
.partner .sq{width:26px;height:26px;background:var(--ink)}

.boat{position:absolute;width:310px;height:305px;background:var(--white);box-shadow:0 2px 10px rgba(0,0,0,.16)}
.boat .pic{position:absolute;left:0;top:0;width:310px;height:246px}
.boat .label{position:absolute;left:0;right:0;top:258px;text-align:center;font-size:18px;color:#222}

.contact{position:absolute;top:3660px;left:0;width:1200px;height:498px}
.form-panel{position:absolute;left:112px;top:0;width:592px;height:498px;background:rgba(23,60,170,.86)}
.field{position:absolute;color:var(--white)}
.field .k{font-size:14px;letter-spacing:.5px}
.field .v{font-size:13px;margin-top:16px;padding-bottom:10px;border-bottom:1px solid rgba(255,255,255,.7)}

.research p{position:absolute;left:112px;top:4330px;width:440px;font-size:13.5px;line-height:32.5px;color:var(--text)}

.footer{position:absolute;top:4760px;left:0;width:1200px;height:439px}
.footer h4{position:absolute;color:var(--red);font:500 20px "Roboto",sans-serif}
.footer ul{list-style:none;position:absolute;left:126px;top:156px}
.footer li{color:var(--white);font-size:13.5px;font-weight:500;line-height:32.5px}
.finfo{position:absolute;left:862px;color:var(--white);font-size:12.5px;line-height:20px;display:flex;gap:18px;align-items:flex-start}
.finfo .ic{width:22px;height:22px;background:var(--white);border-radius:4px;flex:none;display:flex;align-items:center;justify-content:center}
</style>
</head>
<body>

<div class="topbar">
  <div class="item" style="left:112px">
    <span class="icon-box"><svg width="18" height="18" viewBox="0 0 24 24"><rect x="1" y="1" width="22" height="22" rx="4" fill="#fff"/><path d="M7 5l3 3-2 2c1 2 3 4 5 5l2-2 3 3-2 3C10 18 6 14 5 7z" fill="#c0141c"/></svg></span>(555) 014-2290
  </div>
  <div class="sep" style="left:300px"></div>
  <div class="item" style="left:336px">
    <span class="icon-box"><svg width="18" height="18" viewBox="0 0 24 24"><rect x="1" y="1" width="22" height="22" rx="4" fill="#fff"/><path d="M12 4a5 5 0 0 0-5 5c0 4 5 10 5 10s5-6 5-10a5 5 0 0 0-5-5zm0 7a2 2 0 1 1 0-4 2 2 0 0 1 0 4z" fill="#c0141c"/></svg></span>Garland Boats, Inc.&nbsp; 4200 Harbor Rd.&nbsp;&nbsp; Marlow Bay, LA 70999&nbsp; USA
  </div>
  <div class="sep" style="left:840px"></div>
  <div class="item" style="left:884px">
    <span class="icon-box"><svg width="18" height="18" viewBox="0 0 24 24"><rect x="1" y="1" width="22" height="22" rx="4" fill="#fff"/><path d="M5 8h14v9H5z" fill="none" stroke="#c0141c" stroke-width="2"/><path d="M5 8l7 5 7-5" fill="none" stroke="#c0141c" stroke-width="2"/></svg></span>Office@garlandboats.com
  </div>
</div>

<div class="brand">
  <div class="name">GARLAND</div>
  <div class="sub">CUSTOM BOATS</div>
</div>
<div class="reviews">
  <div><span style="display:inline-block;width:26px;height:26px;border-radius:50%;border:4px solid #3b78e7;vertical-align:middle"></span> <span class="stars">★★★★★</span> (1606)</div>
  <div style="margin-top:8px;font-weight:500">Based On ReviewHub reviews</div>
</div>
<div class="search">Search Here
  <svg width="16" height="16" viewBox="0 0 24 24"><circle cx="10" cy="10" r="6" fill="none" stroke="#222" stroke-width="2.4"/><path d="M15 15l6 6" stroke="#222" stroke-width="2.4"/></svg>
</div>

<nav class="nav">
  <ul>
    <li class="active">Home</li><li>Boats</li><li>Contact us</li><li>Links</li><li>Equipment</li><li>Driving Directions</li><li>Packages</li>
  </ul>
  <div class="cta">CUSTOMIZE HERE</div>
</nav>

<section class="hero">
  <svg class="ph" width="1200" height="600" viewBox="0 0 1200 600" role="img" aria-label="Sport fishing yacht running at speed across open blue sea">
    <defs>
      <linearGradient id="sea" x1="0" y1="0" x2="0" y2="1">
        <stop offset="0" stop-color="#5b84b6"/><stop offset=".35" stop-color="#1d4f93"/><stop offset="1" stop-color="#0b2f6b"/>
      </linearGradient>
      <radialGradient id="boatGlow" cx=".7" cy=".45" r=".35">
        <stop offset="0" stop-color="#e9eef6"/><stop offset="1" stop-color="#e9eef6" stop-opacity="0"/>
      </radialGradient>
    </defs>
    <path d="M0 0H1200V290C1140 500 1000 560 700 566C400 572 150 560 0 560Z" fill="url(#sea)"/>
    <path d="M0 0H1200V290C1140 500 1000 560 700 566C400 572 150 560 0 560Z" fill="url(#boatGlow)"/>
    <path d="M1200 260V300C1150 520 1000 580 700 586C450 590 350 582 300 578C450 574 600 572 700 566C1000 560 1140 500 1200 260Z" fill="var(--blue)"/>
  </svg>
  <h1 class="display">Custom Boats.<br>Built to Perform.</h1>
  <div class="btn" style="left:110px;top:230px;width:150px;height:42px">GET STARTED</div>
  <div class="dots"><span></span><span class="on"></span><span></span></div>
</section>

<div class="sec-title" style="top:858px">
  <div class="ghost display">What We Do</div>
  <div class="solid display">What <em>We Do</em></div>
</div>

<div class="card" style="left:112px;top:940px;width:300px;height:396px">
  <div class="pic" style="height:306px;background:linear-gradient(#3d7fc5 0%,#5f9cd4 50%,#0f4aa0 52%,#062f77 100%)" role="img" aria-label="Dive boat seen half above and half below the waterline"></div>
  <div class="label" style="top:340px">Dive Boats</div>
</div>
<div class="card featured" style="left:447px;top:940px;width:252px;height:396px">
  <div class="pic" style="height:272px;background:linear-gradient(#8ec7c4,#3f9a94 55%,#1c6a6b)" role="img" aria-label="Sport fisherman yacht on green shallow water"></div>
  <svg class="abs" style="left:104px;top:254px" width="46" height="46" viewBox="0 0 46 46"><circle cx="23" cy="23" r="22" fill="var(--blue)"/><path d="M11 27h24l-4 6H15z" fill="#fff"/><rect x="19" y="17" width="10" height="8" fill="#fff"/></svg>
  <div class="label" style="top:326px">Yacht Sport Fisherman</div>
</div>
<div class="card" style="left:781px;top:940px;width:310px;height:396px">
  <div class="pic" style="height:306px;background:linear-gradient(#6c9ac6,#2a5f95 40%,#0f3f6f)" role="img" aria-label="Patrol boat cruising through waves"></div>
  <div class="label" style="top:340px">Patrol Boats</div>
</div>

<svg class="ph" style="left:0;top:1428px" width="612" height="522" viewBox="0 0 612 522" role="img" aria-label="Workers polishing an aluminum boat hull in the workshop">
  <defs><linearGradient id="shop" x1="0" y1="0" x2="1" y2="1"><stop offset="0" stop-color="#9aa0a8"/><stop offset=".5" stop-color="#cfd3d8"/><stop offset="1" stop-color="#5d636b"/></linearGradient></defs>
  <path d="M0 0H600V400C600 470 560 522 480 522H0Z" fill="url(#shop)"/>
</svg>
<div class="about-panel">
  <div class="abs display" style="left:-10px;top:30px;width:560px;text-align:right;font-size:70px;color:#c7d6f1">About Us</div>
  <div class="abs display" style="left:44px;top:46px;font-size:42px">About <span style="color:var(--blue)">Us</span></div>
  <p style="top:120px">Garland Custom Boats&nbsp; is a premier manufacturer of custom boats, specializing in the creation of high-quality vessels ranging from 28 to 72 feet in length. With a strong focus on precision and craftsmanship, we design and build boats tailored to meet the diverse needs of our clients.</p>
  <p style="top:280px;left:40px">Our portfolio spans a wide array of markets, featuring everything from sleek recreational fishing boats, ready for adventures on the water, to robust commercial diving vessels designed to thrive in the toughest conditions.</p>
  <div class="btn" style="left:42px;top:436px;width:152px;height:42px">READ MORE</div>
</div>

<section class="partners">
  <h3 class="display">Inboard engines from<br><em>Reputable brands</em></h3>
  <div class="partner" style="left:556px">Harbor Marine</div>
  <div class="partner" style="left:764px;color:var(--blue)">Keelpoint</div>
  <div class="partner" style="left:900px"><span class="sq"></span>Fieldline Marine</div>
</section>

<svg class="ph" style="left:0;top:2175px" width="1200" height="465" viewBox="0 0 1200 465" role="img" aria-label="Video preview: three patrol boats racing side by side across blue water">
  <defs><linearGradient id="vid" x1="0" y1="0" x2="0" y2="1"><stop offset="0" stop-color="#dfe8f3"/><stop offset=".45" stop-color="#b9cbe2"/><stop offset=".55" stop-color="#2a5cae"/><stop offset="1" stop-color="#0c2f75"/></linearGradient></defs>
  <rect width="1200" height="465" fill="url(#vid)"/>
  <circle cx="600" cy="282" r="22" fill="#fff"/>
  <circle cx="600" cy="282" r="15" fill="var(--blue)"/>
  <path d="M595 274l11 8-11 8z" fill="#fff"/>
</svg>

<div class="sec-title" style="top:2718px">
  <div class="ghost display" style="font-size:78px">Our Custom Boats</div>
  <div class="solid display">Our <em>Custom Boats</em></div>
</div>
<div class="abs" style="left:0;top:2790px;width:1200px;text-align:center;font-size:14px;line-height:26px;color:#333">We have built hundreds of boats for all over the world. Please take a moment to look at our boats.<br>We think you'll see the Garland Boats difference!</div>

<div class="boat" style="left:110px;top:2870px"><div class="pic" style="background:linear-gradient(#a9c6e0,#4f8cbd 50%,#1b6a8e)" role="img" aria-label="42 foot dive boat at sea"></div><div class="label">42' Dive Special</div></div>
<div class="boat" style="left:444px;top:2870px"><div class="pic" style="background:linear-gradient(#b5c3cf,#7c98b0 50%,#3b6b83)" role="img" aria-label="46 foot cruiser on calm water"></div><div class="label">46' Bay Cruiser</div></div>
<div class="boat" style="left:778px;top:2870px"><div class="pic" style="background:linear-gradient(#d5dee6,#7a9a6c 40%,#5c7489)" role="img" aria-label="71 foot custom dive boat docked near trees"></div><div class="label">71' Custom Dive</div></div>
<div class="boat" style="left:110px;top:3194px"><div class="pic" style="background:linear-gradient(#cfd8e0,#9cb1c2 55%,#4f6f86)" role="img" aria-label="Boat beside a glacier wall"></div><div class="label">Arctic Runner</div></div>
<div class="boat" style="left:444px;top:3194px"><div class="pic" style="background:linear-gradient(#3c63a8,#2a58a8 50%,#1a3f86)" role="img" aria-label="36 foot dive boat under blue sky"></div><div class="label">36' Dive Special</div></div>
<div class="boat" style="left:778px;top:3194px"><div class="pic" style="background:linear-gradient(#b8c7d4,#8a9aa8 50%,#4e6172)" role="img" aria-label="71 foot custom dive boat at the marina"></div><div class="label">71' Custom Dive</div></div>

<div class="btn" style="left:524px;top:3530px;width:152px;height:44px">VIEW ALL</div>

<section class="contact">
  <div class="ph" style="left:0;top:0;width:1200px;height:498px;background:linear-gradient(#1e4c8e,#0a2b63)" role="img" aria-label="Deep blue ocean water"></div>
  <div class="ph" style="left:704px;top:0;width:496px;height:498px;background:linear-gradient(120deg,#6b88a8,#9fb2c4 40%,#3e4a57)" role="img" aria-label="Angler in red jacket fishing from the deck of a boat"></div>
  <div class="form-panel">
    <div class="abs display" style="left:30px;top:18px;font-size:62px;color:rgba(255,255,255,.16);white-space:nowrap">Contact Us</div>
    <div class="abs display" style="left:30px;top:22px;font-size:42px;color:var(--white)">Contact Us</div>
    <div class="field" style="left:40px;top:118px;width:240px"><div class="k">FULL NAME</div><div class="v">Jhon Smith</div></div>
    <div class="field" style="left:306px;top:118px;width:240px"><div class="k">EMAIL</div><div class="v">info@xyz.com</div></div>
    <div class="field" style="left:40px;top:206px;width:240px"><div class="k">HOTEL NAME</div><div class="v">info@xyz.com</div></div>
    <div class="field" style="left:308px;top:206px;width:240px"><div class="k">INQUIRY TYPE</div><div class="v">+1 888 888 8888</div></div>
    <div class="field" style="left:40px;top:296px;width:460px"><div class="k">MESSAGE</div><div class="v">Hi , Do you have Mpment To Talk About Us</div></div>
    <svg class="abs" style="left:500px;top:340px" width="48" height="48" viewBox="0 0 48 48"><circle cx="24" cy="24" r="23" fill="var(--red)"/><path d="M14 24l20-9-7 20-3-8z" fill="#fff"/></svg>
  </div>
</section>

<section class="research">
  <div class="abs display" style="left:112px;top:4225px;font-size:62px;color:#eceef2;white-space:nowrap">Research Vessels</div>
  <div class="abs display" style="left:118px;top:4234px;font-size:42px">Research <span style="color:var(--blue)">Vessels</span></div>
  <p>In addition to research vessels, we specialize in durable supply boats essential for efficient logistics in remote areas. Our buoy tender boats, designed for the Coastal Ocean Research Agency (CORA), aid in the maintenance and deployment of buoys that are critical for environmental monitoring. Furthermore, we create specialized dive boats customized for specific regions, ensuring they meet the unique demands of local diving activities.</p>
  <div class="btn" style="left:110px;top:4592px;width:152px;height:44px">READ MORE</div>
  <svg class="ph" style="left:642px;top:4250px" width="448" height="428" viewBox="0 0 448 428" role="img" aria-label="Center console research boat speeding over turquoise water">
    <defs><linearGradient id="rv" x1="0" y1="0" x2="0" y2="1"><stop offset="0" stop-color="#3d8a9a"/><stop offset=".5" stop-color="#2a7f86"/><stop offset="1" stop-color="#15536a"/></linearGradient></defs>
    <path d="M0 0H448V250C448 360 380 428 270 428H0Z" fill="url(#rv)"/>
  </svg>
</section>

<footer class="footer">
  <svg class="ph" style="left:0;top:0" width="1200" height="439" viewBox="0 0 1200 439">
    <path d="M0 439V230C40 110 200 40 440 30C600 24 780 30 870 36C700 40 500 44 420 60C230 96 90 170 30 300V439Z" fill="var(--blue)"/>
    <path d="M30 439V300C90 170 230 96 420 60C500 44 700 40 870 36H1200V439Z" fill="#000"/>
  </svg>
  <h4 style="left:124px;top:118px">Quick Links</h4>
  <ul>
    <li>Home</li><li>Boats</li><li>Contact us</li><li>Links</li><li>Equipment</li><li>Driving Directions</li><li>&nbsp;Packages</li>
  </ul>
  <div class="abs" style="left:408px;top:152px;width:390px;text-align:center">
    <div style="font:700 40px 'Roboto',sans-serif;color:var(--blue);letter-spacing:1px">GARLAND</div>
    <div style="font:700 16px 'Roboto',sans-serif;color:var(--blue);letter-spacing:4px;margin-top:2px">CUSTOM BOATS</div>
  </div>
  <div class="abs" style="left:378px;top:262px;width:420px;height:46px;display:flex">
    <div style="flex:1;background:#fff;font-size:12px;color:#555;display:flex;align-items:center;padding-left:20px">Enter Email Address</div>
    <div style="width:126px;background:var(--blue);color:#fff;font-weight:700;font-size:15px;display:flex;align-items:center;justify-content:center;border-radius:0 20px 0 0">SUBSCRIBE</div>
  </div>
  <h4 style="left:858px;top:118px">Contact Info</h4>
  <div class="finfo" style="top:168px"><span class="ic"><svg width="14" height="14" viewBox="0 0 24 24"><path d="M12 2a7 7 0 0 0-7 7c0 5 7 13 7 13s7-8 7-13a7 7 0 0 0-7-7zm0 10a3 3 0 1 1 0-6 3 3 0 0 1 0 6z"/></svg></span><span>Garland Boats, Inc. 4200 Harbor Rd. Marlow Bay,<br>LA 70999 USA</span></div>
  <div class="finfo" style="top:228px"><span class="ic"><svg width="14" height="14" viewBox="0 0 24 24"><path d="M6 3l4 4-2 3c1 3 3 5 6 6l3-2 4 4-3 3C10 21 3 14 3 6z"/></svg></span><span>(555) 014-2290</span></div>
  <div class="finfo" style="top:280px"><span class="ic"><svg width="14" height="14" viewBox="0 0 24 24"><path d="M3 6h18v12H3z" fill="none" stroke="#000" stroke-width="2"/><path d="M3 6l9 7 9-7" fill="none" stroke="#000" stroke-width="2"/></svg></span><span>Office@garlandboats.com</span></div>
  <div class="abs" style="left:0;top:418px;width:1200px;text-align:center;color:#fff;font-size:12.5px">© 2025&nbsp; Garland Custom Boats. All rights reserved.</div>
</footer>

</body>
</html>
```